Exciting & Elegant Stationary Pack

Stationary consists of
1. Letter head / Envelope
2. Business Card
3. Invoice
4. 40x40mm sticker

Attached files;

1. Logo (Other formats available on request)
2. MS word Doc - For information and description of design
3. Website image (This will be our new website so use the colours so everything ties together)
4. Sample of stationary pack we like, but feel free to be creative

Target Market(s)

Home improvement

Industry/Entity Type

Construction

Font styles to use
Other font styles liked:
• Leave up to designer - We like font used on (website attached image)

Requirements
Must have
• Please look at uploaded file of sample website and use colours
Nice to have
• Any type of business card design - eg. metal, die cut, embossed, etc...

```html
<!DOCTYPE html>
<html lang="en">
<head>
<meta charset="utf-8">
<title>Tessera Tiling – Business Card</title>
<link href="https://fonts.googleapis.com/css2?family=PT+Sans:wght@400;700&family=PT+Sans+Narrow:wght@400;700&display=swap" rel="stylesheet">
<style>
  :root {
    --navy: #143f67;
    --orange: #f08a3a;
    --white: #ffffff;
    --backdrop: #7a7a7a;
    --social-blue: #3b5b9a;
    --social-red: #dc4a38;
    --social-dark: #333333;
  }
  * { box-sizing: border-box; margin: 0; padding: 0; }
  html, body { width: 1200px; height: 1124px; overflow: hidden; }
  body {
    background: var(--backdrop);
    font-family: "PT Sans", sans-serif;
    position: relative;
  }
  .card {
    position: absolute;
    width: 694px;
    height: 396px;
    overflow: hidden;
  }
  /* Front */
  .card-front { left: 97px; top: 153px; background: var(--white); }
  .front-top { position: absolute; left: 0; top: 0; width: 100%; height: 226px; }
  .front-rule { position: absolute; left: 0; top: 226px; width: 100%; height: 4px; background: var(--orange); }
  .front-bottom { position: absolute; left: 0; top: 230px; width: 100%; bottom: 0; background: var(--navy); color: var(--white); }

  .brand {
    position: absolute; left: 34px; top: 52px;
    display: flex; align-items: center; gap: 12px;
    color: var(--navy);
    font-family: "PT Sans", sans-serif; font-weight: 700;
    font-size: 38px; letter-spacing: 1px; text-transform: uppercase;
  }
  .brand-square { width: 22px; height: 22px; background: var(--navy); }

  .connect { position: absolute; right: 58px; top: 76px; text-align: center; }
  .connect-title {
    font-family: "PT Sans Narrow", sans-serif; font-weight: 700;
    font-size: 28px; color: var(--navy);
  }
  .social-list { display: flex; justify-content: center; gap: 18px; margin-top: 12px; }
  .social-dot { width: 41px; height: 41px; border-radius: 50%; }
  .social-dot.blue { background: var(--social-blue); }
  .social-dot.red { background: var(--social-red); }
  .social-dot.dark { background: var(--social-dark); }

  .person { position: absolute; left: 70px; top: 54px; }
  .person-name { font-weight: 700; font-size: 24px; }
  .person-role { font-family: "PT Sans Narrow", sans-serif; font-size: 17px; margin-top: 2px; }

  .contact { position: absolute; right: 40px; top: 26px; text-align: right; font-size: 18px; line-height: 26px; }
  .contact-row { display: flex; justify-content: flex-end; align-items: center; gap: 12px; }
  .contact-row svg { width: 20px; height: 20px; flex: none; }
  .contact-row .no-icon { width: 20px; }

  /* Back */
  .card-back { left: 349px; top: 615px; background: var(--navy); }
  .tile-field { position: absolute; inset: 0; background: var(--navy); }
  .back-brand {
    position: absolute; right: 34px; bottom: 50px;
    color: var(--white); font-weight: 700; font-size: 38px;
    letter-spacing: 1px; text-transform: uppercase;
  }
</style>
</head>
<body>

<section class="card card-front">
  <div class="front-top">
    <div class="brand"><span class="brand-square"></span>Tessera Tiling</div>
    <div class="connect">
      <p class="connect-title">Connect with us</p>
      <div class="social-list">
        <span class="social-dot blue"></span>
        <span class="social-dot red"></span>
        <span class="social-dot dark"></span>
      </div>
    </div>
  </div>
  <div class="front-rule"></div>
  <div class="front-bottom">
    <div class="person">
      <p class="person-name">Linh Pham</p>
      <p class="person-role">Project Manager</p>
    </div>
    <div class="contact">
      <p class="contact-row">Lic No.,204519k<span class="no-icon"></span></p>
      <p class="contact-row">0400 555 012
        <svg viewBox="0 0 20 20" fill="none" stroke="#fff" stroke-width="1.8"><rect x="5" y="1.5" width="10" height="17" rx="2"/><line x1="9" y1="15.5" x2="11" y2="15.5"/></svg>
      </p>
      <p class="contact-row">hello@tesseratiling.com.au
        <svg viewBox="0 0 20 20"><rect x="2" y="5" width="16" height="11" fill="#fff"/><polyline points="2,5 10,11 18,5" fill="none" stroke="#143f67" stroke-width="1.5"/></svg>
      </p>
      <p class="contact-row">www.tesseratiling.com.au
        <svg viewBox="0 0 20 20" fill="none" stroke="#fff" stroke-width="1.6"><circle cx="10" cy="10" r="8"/><ellipse cx="10" cy="10" rx="3.5" ry="8"/><line x1="2" y1="10" x2="18" y2="10"/></svg>
      </p>
    </div>
  </div>
</section>

<section class="card card-back">
  <div class="tile-field" role="img" aria-label="Navy tiled wall pattern of offset rectangular tiles"></div>
  <p class="back-brand">Tessera Tiling</p>
</section>

</body>
</html>
```